Meadowfield Baptist Church Banner Design

Designing 6 banners (3 + 3 that will hang on opposite sides of our auditorium) that are 10 feet long by 4 feet wide.

Use our branding guide - specifically item 4 (vertical logo) and item 5 (icon logo).

Design elements found in our KINDLE booklet, we would like to see designs that utilize the white, green and blue colour palettes but NOT the grey. Other colours may be incorporated (e.g. coral).

We are looking for 3 banner designs that would match on either side of the auditorium, the first banner incorporating the word "TRUTH", the second incorporating the word "LOVE", and the third incorporating the word "MISSION".

We interested in incorporating graphics such as trees or outdoor themes.

Font styles to use
Other font styles liked:
• Montserrat

Colors
34a7d7
00a990
f47c35

Requirements
Must have
• Banner Type #1 include the word "TRUTH"
Banner Type #2 include the word "LOVE"
Banner Type #3 include the word "MISSION"

Colour scheme must include CMYK 54 / 5 / 16 / 0 (which is available in the branding guide.) We have selected the three colours, included below in the brief.

From the branding guide - utilize #5 (icon) for the banner.

UPDATE: After reviewing the initial submissions, we are asking for designs that ONLY incorporate #5 - the ICON logo for the banners.
Nice to have
• It would be nice to have some creativity with the colour ... though a more minimalistic style is preferred.

Graphic adaptations such as trees in the background would be of interest.
Should not have
• Colour scheme should not be gray scale.

The banners should NOT be too busy.

Scripture verses (written out) are not necessary.

```html
<!DOCTYPE html>
<html lang="en">
<head>
<meta charset="utf-8">
<title>Meadowfield Baptist Church – Auditorium Banners</title>
<link rel="stylesheet" href="https://fonts.googleapis.com/css2?family=Montserrat:wght@600;800&display=swap">
<style>
  :root {
    --stage: #535353;
    --banner-edge: #9a9a9a;
    --paper: #ffffff;
    --word: #ffffff;
    --brand-teal: #6cc3d5;

    --truth-light: #fcb38c;
    --truth-mid: #f49a6a;
    --truth-deep: #e07a46;

    --love-light: #6ec2ee;
    --love-mid: #3aabe2;
    --love-deep: #0e92cc;

    --mission-light: #6fcdc6;
    --mission-mid: #3dbbae;
    --mission-deep: #05a792;
  }

  * { box-sizing: border-box; margin: 0; padding: 0; }

  html, body {
    width: 1200px;
    height: 944px;
    overflow: hidden;
    background: var(--stage);
  }

  .artboard {
    position: relative;
    width: 1200px;
    height: 944px;
  }

  .banner {
    position: absolute;
    top: 43px;
    width: 340px;
    height: 854px;
    background: var(--paper);
    border: 1px solid var(--banner-edge);
    overflow: hidden;
  }
  .banner--truth   { left: 51px; }
  .banner--love    { left: 431px; }
  .banner--mission { left: 816px; }

  .banner__scene {
    position: absolute;
    left: 0;
    top: 0;
    width: 100%;
    height: 647px;
  }
  .banner--truth .banner__scene {
    background: linear-gradient(180deg, var(--truth-light) 0%, var(--truth-mid) 55%, var(--truth-deep) 100%);
  }
  .banner--love .banner__scene {
    background: linear-gradient(180deg, var(--love-light) 0%, var(--love-mid) 55%, var(--love-deep) 100%);
  }
  .banner--mission .banner__scene {
    background: linear-gradient(180deg, var(--mission-light) 0%, var(--mission-mid) 55%, var(--mission-deep) 100%);
  }

  .banner__word {
    position: absolute;
    top: 86px;
    left: 50%;
    writing-mode: vertical-rl;
    transform: translateX(-50%) rotate(180deg);
    font-family: "Montserrat", sans-serif;
    font-weight: 800;
    font-size: 112px;
    line-height: 1;
    letter-spacing: 1px;
    color: var(--word);
    white-space: nowrap;
  }

  .banner__footer {
    position: absolute;
    left: 0;
    bottom: 0;
    width: 100%;
    height: 207px;
    display: flex;
    align-items: center;
    justify-content: center;
    gap: 12px;
  }

  .brand__dot {
    width: 16px;
    height: 16px;
    border-radius: 50%;
    background: var(--brand-teal);
    flex: none;
  }

  .brand__name {
    font-family: "Montserrat", sans-serif;
    font-weight: 600;
    font-size: 19px;
    line-height: 1.25;
    color: var(--brand-teal);
    text-align: left;
  }
</style>
</head>
<body>
  <main class="artboard">

    <section class="banner banner--truth">
      <div class="banner__scene" role="img" aria-label="Illustration of a stylised leafy tree over rolling hills in coral tones"></div>
      <h2 class="banner__word">TRUTH</h2>
      <footer class="banner__footer">
        <span class="brand__dot"></span>
        <p class="brand__name">Meadowfield<br>Baptist Church</p>
      </footer>
    </section>

    <section class="banner banner--love">
      <div class="banner__scene" role="img" aria-label="Illustration of a stylised leafy tree over rolling hills in blue tones"></div>
      <h2 class="banner__word">LOVE</h2>
      <footer class="banner__footer">
        <span class="brand__dot"></span>
        <p class="brand__name">Meadowfield<br>Baptist Church</p>
      </footer>
    </section>

    <section class="banner banner--mission">
      <div class="banner__scene" role="img" aria-label="Illustration of a stylised leafy tree over rolling hills in green tones"></div>
      <h2 class="banner__word">MISSION</h2>
      <footer class="banner__footer">
        <span class="brand__dot"></span>
        <p class="brand__name">Meadowfield<br>Baptist Church</p>
      </footer>
    </section>

  </main>
</body>
</html>
```